KAJU Freightways #ALLKAJU Business Cards & Letterhead

I am looking to business cards designed for our organization. We are currently undergoing a small re-branding that is taking place. Our organization is called KAJU Freightways and we are headquartered in Phoenix, AZ. We primarily provide transportation and logistics services to the Marlow Parcel Bureau who is our largest customer. I would like to see a design that incorporates name, title, contact info, website, and address (this will be different depending on the employee). I would also like to see some color on the business card using our logo colors or a variation. I would like our logo on the back of the business card with the website displayed. The final design should communicate that we are a next generation transportation operate that focuses on being driver-first, customer-centric, innovative, and sustainable.We would also like our #ALLKAJU catch phrase incorporated as well.

Target Market(s)

Transportation & Logistics

Industry/Entity Type

Trucking Company

Contact Information for Business Card

-First and Last Name
-Position Title
-Contact Phone
-Contact Email
-Physical Address

Font styles to use
Serif

Colors

Designer to choose colors to be used in the design.

Requirements
Must have
• -KAJU logo prominently displayed
• -#ALLKAJU catch phrase used
• -Some amount of color, design gradient, etc.
• -Logo on the back with website listed (https://www.kajufreightco.example)

```html
<!DOCTYPE html>
<html lang="en">
<head>
<meta charset="utf-8">
<title>KAJU Freightways – Business Card &amp; Letterhead</title>
<link rel="stylesheet" href="https://fonts.googleapis.com/css2?family=Roboto:wght@400;500;700&family=Fira+Sans+Condensed:ital,wght@1,500&display=swap">
<style>
  :root {
    --green: #82c341;
    --navy: #0b3a45;
    --grey-text: #5a5a5a;
    --backdrop: #999999;
    --paper: #ffffff;
    --edge: #7d7d7d;
  }
  * { box-sizing: border-box; margin: 0; padding: 0; }
  html, body { width: 1200px; height: 763px; overflow: hidden; }
  body {
    background: var(--backdrop);
    font-family: "Roboto", Arial, sans-serif;
    position: relative;
  }

  .card {
    position: absolute;
    left: 91px;
    width: 399px;
    height: 234px;
    border-radius: 9px;
    border: 1px solid var(--edge);
    overflow: hidden;
  }
  .card-front { top: 134px; background: var(--paper); }
  .card-back { top: 390px; background: var(--green); }

  .brand {
    position: absolute;
    display: flex;
    align-items: center;
    justify-content: center;
    gap: 6px;
    font-weight: 700;
    color: var(--navy);
    letter-spacing: 1px;
    line-height: 1;
  }
  .brand-dot { border-radius: 50%; background: var(--green); flex: none; }

  .card-front .brand { left: 30px; top: 91px; width: 160px; font-size: 34px; }
  .card-front .brand-dot { width: 14px; height: 14px; }

  .tagline {
    position: absolute;
    font-family: "Fira Sans Condensed", "Arial Narrow", sans-serif;
    font-style: italic;
    font-weight: 500;
    color: var(--green);
    white-space: nowrap;
    text-align: center;
  }
  .card-front .tagline { left: 30px; width: 160px; top: 157px; font-size: 9.6px; }

  .divider {
    position: absolute;
    left: 199px; top: 64px;
    width: 1px; height: 105px;
    background: #bdbdbd;
  }

  .contact { position: absolute; color: var(--grey-text); white-space: nowrap; }
  .card-front .contact { left: 215px; top: 64px; font-size: 9.8px; line-height: 12px; }
  .person-name { color: var(--navy); font-weight: 700; font-size: 13px; line-height: 15px; letter-spacing: 0.3px; }
  .person-title { color: var(--green); font-size: 10px; line-height: 12px; }
  .address { margin-top: 7px; }
  .contact-lines { margin-top: 7px; line-height: 13px; }
  .contact-line { display: flex; align-items: center; gap: 3px; }
  .icon { width: 8px; height: 8px; flex: none; }

  .footer-band { position: absolute; left: 0; bottom: 0; display: block; }
  .hashtag {
    position: absolute;
    color: var(--green);
    font-weight: 700;
    letter-spacing: 0.4px;
    white-space: nowrap;
    transform: translateX(-50%);
  }
  .card-front .hashtag { left: 334px; top: 214px; font-size: 9.6px; }

  .card-back .brand {
    left: 0; width: 399px; top: 100px;
    font-size: 32px; color: var(--paper);
  }
  .card-back .brand-dot { width: 13px; height: 13px; background: var(--paper); }
  .back-web {
    position: absolute;
    left: 0; width: 399px; top: 207px;
    text-align: center;
    color: var(--paper);
    font-size: 10.5px;
  }
  .back-web b { font-weight: 500; }

  .letterhead {
    position: absolute;
    left: 523px; top: 17px;
    width: 570px; height: 725px;
    background: var(--paper);
    border: 1px solid var(--edge);
    overflow: hidden;
  }
  .letterhead .brand { left: 35px; top: 47px; width: 100px; font-size: 22px; gap: 4px; }
  .letterhead .brand-dot { width: 9px; height: 9px; }
  .letterhead .tagline { left: 35px; width: 100px; top: 90px; font-size: 6.2px; }
  .letterhead .contact { left: 406px; top: 35px; font-size: 8px; line-height: 10px; }
  .letterhead .contact-lines { margin-top: 6px; line-height: 11px; }
  .letterhead .icon { width: 6.5px; height: 6.5px; }
  .letterhead .hashtag { left: 481px; top: 705px; font-size: 11.5px; }
</style>
</head>
<body>

<section class="card card-front" aria-label="Business card front">
  <div class="brand"><span class="brand-dot"></span>KAJU</div>
  <p class="tagline">Transportation and Logistics Services</p>
  <div class="divider"></div>
  <div class="contact">
    <p class="person-name">ROWAN HALE</p>
    <p class="person-title">President</p>
    <p class="address">4120 North Cinder Ridge Road<br>Phoenix, AZ 85009</p>
    <div class="contact-lines">
      <p class="contact-line">
        <svg class="icon" viewBox="0 0 10 10"><path d="M2 0.5 L3.8 2.6 L2.9 3.8 Q4 6 6.2 7.1 L7.4 6.2 L9.5 8 L8.3 9.5 Q3 9 0.5 1.7 Z" fill="var(--green)"/></svg>
        555-014-2290
      </p>
      <p class="contact-line">
        <svg class="icon" viewBox="0 0 10 10"><rect x="0.5" y="2" width="9" height="6.5" fill="var(--green)"/><path d="M0.8 2.3 L5 5.8 L9.2 2.3" fill="none" stroke="#fff" stroke-width="0.9"/></svg>
        info@kajufreightco.example
      </p>
      <p class="contact-line">
        <svg class="icon" viewBox="0 0 10 10"><circle cx="5" cy="5" r="4.3" fill="none" stroke="var(--green)" stroke-width="0.9"/><ellipse cx="5" cy="5" rx="1.8" ry="4.3" fill="none" stroke="var(--green)" stroke-width="0.8"/><path d="M0.7 5 H9.3" stroke="var(--green)" stroke-width="0.8"/></svg>
        www.kajufreightco.example
      </p>
    </div>
  </div>
  <svg class="footer-band" width="399" height="22" viewBox="0 0 399 22">
    <polygon points="0,12 269,12 260,22 0,22" fill="var(--green)"/>
    <polygon points="284,0 399,0 399,22 263,22" fill="var(--navy)"/>
  </svg>
  <span class="hashtag">#ALLKAJU</span>
</section>

<section class="card card-back" aria-label="Business card back">
  <div class="brand"><span class="brand-dot"></span>KAJU</div>
  <p class="back-web">www.<b>kajufreightco</b>.example</p>
</section>

<section class="letterhead" aria-label="Letterhead">
  <div class="brand"><span class="brand-dot"></span>KAJU</div>
  <p class="tagline">Transportation and Logistics Services</p>
  <div class="contact">
    <p>4120 North Cinder Ridge Road<br>Phoenix, AZ 85009</p>
    <div class="contact-lines">
      <p class="contact-line">
        <svg class="icon" viewBox="0 0 10 10"><path d="M2 0.5 L3.8 2.6 L2.9 3.8 Q4 6 6.2 7.1 L7.4 6.2 L9.5 8 L8.3 9.5 Q3 9 0.5 1.7 Z" fill="var(--green)"/></svg>
        555-014-2290
      </p>
      <p class="contact-line">
        <svg class="icon" viewBox="0 0 10 10"><rect x="0.5" y="2" width="9" height="6.5" fill="var(--green)"/><path d="M0.8 2.3 L5 5.8 L9.2 2.3" fill="none" stroke="#fff" stroke-width="0.9"/></svg>
        info@kajufreightco.example
      </p>
      <p class="contact-line">
        <svg class="icon" viewBox="0 0 10 10"><circle cx="5" cy="5" r="4.3" fill="none" stroke="var(--green)" stroke-width="0.9"/><ellipse cx="5" cy="5" rx="1.8" ry="4.3" fill="none" stroke="var(--green)" stroke-width="0.8"/><path d="M0.7 5 H9.3" stroke="var(--green)" stroke-width="0.8"/></svg>
        www.kajufreightco.example
      </p>
    </div>
  </div>
  <svg class="footer-band" width="570" height="28" viewBox="0 0 570 28">
    <polygon points="0,14 383,14 371,28 0,28" fill="var(--green)"/>
    <polygon points="404,0 570,0 570,28 376,28" fill="var(--navy)"/>
  </svg>
  <span class="hashtag">#ALLKAJU</span>
</section>

</body>
</html>
```